Tellmora Corporate Stationery

Look for design of all new corporate stationery for an existing insurance broking business that is going through a redesign and move from older partners to younger family members. New Logo is attached. Company is Brisbane based.
Colours in the Logo is Hex #43bed8 and website features a lot of hex #17b8d8. Website front page "A plan to protect you" - headline. "Professional and Individual advice to protect your greatest assets" - tagline.

Stationery required: Business Cards, Letter head, Thank-you cards, Birthday cards, Presentation folders, With Compliment slips and a powerpoint template. We also would like to send a card to all customers with the something along of the lines of "something new".

Target Market(s)

Customers of Insurance business looking at superannuation, life and income protection insurance, investment advice and wills

Industry/Entity Type

Insurance Broker

Font styles to use
Other font styles liked:
• same as logo

Requirements
Must have
• The above designs for new stationery for the new business including:
• Business Cards, Letter head, Thank-you cards, Birthday cards, Presentation folders, With Compliment slips and a powerpoint template. We also would like to send a card to all customers with the something along of the lines of "something new".
Nice to have
• It is a new look - long time family business being passed to next generation - big focus on advice for YOU, individual advice etc..

```html
<!DOCTYPE html>
<html lang="en">
<head>
<meta charset="utf-8">
<title>Tellmora Business Card</title>
<link href="https://fonts.googleapis.com/css2?family=Open+Sans:ital,wght@0,400;0,600;1,400&display=swap" rel="stylesheet">
<style>
  :root {
    --backdrop: #1e1e1f;
    --card-white: #ffffff;
    --card-grey: #818285;
    --brand-cyan: #43bed8;
    --text-grey: #6d6e71;
    --text-dark: #4a4b4d;
    --white: #ffffff;
  }
  * { margin: 0; padding: 0; box-sizing: border-box; }
  html, body {
    width: 1200px; height: 987px; overflow: hidden;
    background: var(--backdrop);
    font-family: "Open Sans", Arial, sans-serif;
  }
  .canvas { position: relative; width: 1200px; height: 987px; }
  .card {
    position: absolute; width: 615px; height: 352px;
    box-shadow: 0 6px 18px rgba(0,0,0,.45);
  }
  .card--front { left: 293px; top: 130px; background: var(--card-white); }
  .card--back { left: 292px; top: 505px; background: var(--card-grey); }

  .accent-tab {
    position: absolute; left: 0; top: 66px; width: 11px; height: 68px;
    background: var(--brand-cyan); border-radius: 0 6px 6px 0;
  }
  .contact { position: absolute; left: 37px; top: 64px; color: var(--text-dark); }
  .contact__name {
    font-size: 22px; font-weight: 600; color: var(--brand-cyan);
    letter-spacing: .3px; line-height: 28px;
  }
  .contact__role { font-size: 16px; color: var(--text-grey); line-height: 21px; }
  .contact__email { font-size: 16px; line-height: 22px; }
  .contact__phones { margin-top: 15px; list-style: none; }
  .contact__phones li {
    display: flex; align-items: center; gap: 8px;
    font-size: 16px; line-height: 23.5px;
  }
  .contact__phones svg { width: 14px; height: 16px; fill: var(--brand-cyan); }
  .contact__address { margin-top: 20px; font-size: 16px; line-height: 22px; font-style: normal; }
  .contact__web {
    font-size: 16px; line-height: 22px; color: var(--brand-cyan); letter-spacing: 2.4px;
  }

  .brand { position: absolute; display: flex; flex-direction: column; align-items: center; }
  .brand--front { left: 300px; top: 112px; width: 260px; }
  .brand__dot { border-radius: 50%; }
  .brand--front .brand__dot { width: 58px; height: 58px; background: var(--brand-cyan); }
  .brand--front .brand__name {
    margin-top: 18px; font-size: 36px; font-weight: 600;
    color: var(--brand-cyan); letter-spacing: 2px;
  }
  .brand--back { left: 0; top: 100px; width: 615px; }
  .brand--back .brand__dot { width: 110px; height: 110px; background: var(--white); }
  .brand--back .brand__name {
    margin-top: 18px; font-size: 30px; font-weight: 600;
    color: var(--white); letter-spacing: 2px;
  }
  .back__web {
    position: absolute; left: 0; top: 292px; width: 615px; text-align: center;
    font-size: 16px; font-style: italic; color: var(--white); letter-spacing: 5px;
  }
</style>
</head>
<body>
<main class="canvas">
  <section class="card card--front">
    <div class="accent-tab"></div>
    <div class="contact">
      <p class="contact__name">DANIEL REYES</p>
      <p class="contact__role">CEO/FOUNDER</p>
      <p class="contact__email">hello@tellmora.com</p>
      <ul class="contact__phones">
        <li>
          <svg viewBox="0 0 14 16" aria-hidden="true"><path d="M3 1l3 3-1.6 2c.8 2 2.3 3.6 4.3 4.5L10.6 9l3 3-2 2.5C6 14 1 9 .8 3.2z"/></svg>
          617 402 1185
        </li>
        <li>
          <svg viewBox="0 0 14 16" aria-hidden="true"><path d="M3 0h8a1.5 1.5 0 0 1 1.5 1.5v13A1.5 1.5 0 0 1 11 16H3a1.5 1.5 0 0 1-1.5-1.5v-13A1.5 1.5 0 0 1 3 0zm.5 2v10.5h7V2zM7 13.3a.9.9 0 1 0 0 1.8.9.9 0 0 0 0-1.8z"/></svg>
          617 559 2073
        </li>
        <li>
          <svg viewBox="0 0 14 16" aria-hidden="true"><path d="M3 2h8v4H3zM1 7h12a1 1 0 0 1 1 1v5H0V8a1 1 0 0 1 1-1zm2 7h8v1.5H3z"/></svg>
          617 330 4816
        </li>
      </ul>
      <address class="contact__address">214 Harbour Street<br>Brisbane, QLD 4000</address>
      <p class="contact__web">www.tellmora.com</p>
    </div>
    <div class="brand brand--front">
      <span class="brand__dot"></span>
      <span class="brand__name">TELLMORA</span>
    </div>
  </section>

  <section class="card card--back">
    <div class="brand brand--back">
      <span class="brand__dot"></span>
      <span class="brand__name">TELLMORA</span>
    </div>
    <p class="back__web">www.tellmora.com</p>
  </section>
</main>
</body>
</html>
```